Web design for new streaming audio service

We need a homepage design for a new streaming audio service. Our company is called Dunmoral, and we’re basically Vexlo for Audiobooks, Stand-Up Comedy, Lectures, Language Learning, etc. Essentially like Plumtrek for everything audio EXCEPT music.
You don’t have to code the homepage (Design Only), but it should include 3 different designs to work with 1) Web; 2) Phones; 3) Tablets.
Below is a link to a mockup of the web version which gives a good idea of what elements we want. This is just a mockup and we want you to improve it.
Once you download the mockup, please refer to the more detailed instructions below:
The following outlines the design project for the Dunmoral homepage. We have provided a rough mockup of the homepage layout that gives you a general idea of what we’re going for. There are a few elements that we are attached to, and many others where you have complete creative freedom to do whatever you think looks good.
The ZIP file includes the following:
* Mockup to see what we have in mind (dunmoral-homepage-mockup.jpg)
* Text used (dunmoral-homepage-text.txt)
* Raw image of actor (dunmoral-actor1.jpg)
* Raw images for samples (dunmoral-sample-[name].jpg)
Although we have only provided a mockup layout for the web version, we also need you to provide a mobile phone and a tablet version of the design also. It’s very possible the tablet version may be substantially similar to the web version, but the mobile phone version will likely be much different.
All of the raw files are included in the attached ZIP file. Please use our photographs and text as provided although cropping, sizing, etc. is flexible per the instructions below.
Display Requirements:
* Web Version - Minimum resolution 1024x768 (72 dpi) but should look good on 1920x1080 (72 dpi) - Page should be designed to scale to look acceptable in all resolutions in between.
* Phone Version - Minimum Zarno 4 - 640x960 (326 dpi) but should look good on Harlow Quasar T5 - 1920x1080 (441 dpi) - Page should be designed to scale to look acceptable in all resolutions and devices in between.
* Tablet Version - Minimum Bristly Ember QX 7” - 1280x800 (216 dpi) but should also look good on a Tavo Breeze - 2048x1536 (264 dpi) - Page should be designed to scale to look acceptable in all resolutions and devices in between.
Above the Fold - We want to make sure the Dunmoral logo, Member Login Link, Large Photo, Headline, Price, Button, and the first row of sample images are all “Above the fold”. As a general guideline, this means 600 pixels high on a 1024x768 72 dpi web screen. This requirement is less important on Phone versions.
Top Logo Bar - We want to retain the blue bar with the Dunmoral logo on the page, although we are open to a different size, shape and positioning if it greatly enhances the design. Please use the standard logo color, although you are welcome to use either the horizontal or vertical orientation of the logo based on your design.
Text color, font and size - Feel free to design the text in anyway you choose as long as the text is readable on the target platforms.
Buttons - Feel free to use any size, shape and colors for the buttons as long as they are obvious and clickable relative to the page. The only exception is the Chatterly button should follow the Chatterly color scheme and logo treatment (the mockup doesn’t seem 100% correct.)
Top Photograph - We want to retain the large photograph across the top of the screen although final shape and dimensions are flexible.
Size and shape of content samples (i.e. Audiobooks, Stand-Up Comedy, etc.) - Feel free to design the content samples in anyway you choose.
Three Sales Points (i.e. Listen on your Zarno…, All you can enjoy…, etc.) - The Three Sales Points are envisioned to each have a corresponding illustration which you should provide and have rights for. The placeholder is represented by a square next to the text. The color size and shape of these elements are flexible and can be designed in any way you choose.
Opt-in form - Feel free to design the opt-in form in anyway you choose as long as the text is readable and the interactivity is obvious on the target platforms.
Text links and copyright notice - Feel free to design the bottom of the page text links and copyright notice in anyway you choose.
Additional colors, graphic design elements, etc. - Feel free to use any additional colors, graphic design elements, etc. to support your design.
people who want to listen to audio through their mobile devices.
Graphic Design

```html
<!DOCTYPE html>
<html lang="en">
<head>
<meta charset="utf-8">
<title>Dunmoral – Unlimited Listening</title>
<link rel="stylesheet" href="https://fonts.googleapis.com/css2?family=Open+Sans:wght@400;600;700&display=swap">
<style>
:root{
  --blue:#2f8fd0;
  --blue-dark:#1d5f96;
  --navy:#1f3550;
  --sky:#d8ecf8;
  --orange:#f28c1a;
  --orange-dark:#d9720a;
  --grey-bg:#eef1f4;
  --grey-line:#d6dce2;
  --text:#4a5560;
  --white:#ffffff;
}
*{margin:0;padding:0;box-sizing:border-box}
html,body{width:867px;height:1200px;overflow:hidden;background:var(--white)}
body{font-family:"Open Sans",Arial,sans-serif;color:var(--text);position:relative}

/* Hero */
.hero{position:absolute;left:0;top:0;width:867px;height:392px;
  background:linear-gradient(90deg,#f4f8fb 0%,#eef3f7 40%,#e6ddd3 60%,#c9a88e 80%,#8a6a55 100%);overflow:hidden}
.hero-photo{position:absolute;right:0;top:0;width:500px;height:392px;
  background:radial-gradient(ellipse at 55% 45%,#d9b59a 0%,#b88d70 35%,#6e5242 70%,rgba(110,82,66,0) 100%)}
.topbar{position:absolute;left:0;top:0;width:867px;height:70px;background:rgba(216,236,248,.85);
  border-bottom:3px solid var(--blue)}
.logo{position:absolute;left:30px;top:20px;display:flex;align-items:center;gap:10px;
  font-size:24px;font-weight:700;color:var(--blue)}
.logo-mark{width:22px;height:22px;border-radius:50%;background:var(--blue)}
.login{position:absolute;right:30px;top:20px;height:30px;padding:0 16px;background:var(--orange);
  color:var(--white);font-size:12px;font-weight:600;line-height:30px;border-radius:3px}
.hero-copy{position:absolute;left:40px;top:142px}
.headline{font-size:38px;font-weight:600;color:var(--navy);line-height:44px}
.subline{font-size:38px;font-weight:600;color:var(--blue);line-height:44px}
.price{margin-top:14px;font-size:19px;font-weight:700;color:var(--orange)}
.cta{display:inline-block;margin-top:10px;height:42px;padding:0 22px;background:var(--orange);
  color:var(--white);font-size:19px;font-weight:600;line-height:42px;border-radius:3px;
  border-bottom:3px solid var(--orange-dark)}
.cta-note{margin-top:8px;font-size:10px;color:#7d8790}
.dots{position:absolute;left:412px;top:362px;display:flex;gap:8px}
.dots span{width:10px;height:10px;border-radius:50%;background:rgba(255,255,255,.6)}
.dots span.on{background:var(--white)}

/* Samples */
.samples-title{position:absolute;left:0;top:420px;width:867px;text-align:center;
  font-size:26px;font-weight:400;color:var(--blue)}
.grid{position:absolute;left:78px;top:500px;width:740px;display:grid;
  grid-template-columns:repeat(4,170px);column-gap:20px;row-gap:26px}
.tile{width:170px}
.tile-img{width:170px;height:122px;border-radius:3px}
.tile-label{margin-top:8px;text-align:center;font-size:13px;font-weight:600;color:var(--navy)}

/* Sales points */
.points{position:absolute;left:78px;top:878px;width:740px;display:flex;gap:20px}
.point{flex:1;height:80px;background:var(--blue);border-radius:3px;display:flex;align-items:center;
  gap:12px;padding:0 14px;color:var(--white)}
.point-art{flex:none;width:50px;height:50px;border-radius:3px;background:#7fbfe8}
.point p{font-size:12px;line-height:16px}
.point b{display:block;font-size:11px;font-weight:700;margin-top:3px}

/* Opt-in */
.optin{position:absolute;left:78px;top:982px;width:740px;height:128px;background:var(--grey-bg);
  border:1px solid var(--grey-line);border-radius:3px;text-align:center}
.optin h2{margin-top:14px;font-size:20px;font-weight:600;color:var(--blue)}
.optin-note{margin:6px auto 0;width:560px;font-size:10px;line-height:14px;color:#6b7580}
.optin-note a{color:var(--orange);text-decoration:none}
.form-row{margin-top:10px;display:flex;justify-content:center;align-items:center;gap:10px}
.email{width:300px;height:32px;border:1px solid var(--grey-line);background:var(--white);
  border-radius:3px;text-align:left;padding-left:10px;font-size:11px;line-height:30px;color:#9aa3ab}
.btn-access{height:32px;padding:0 14px;background:var(--navy);color:var(--white);font-size:12px;
  font-weight:600;line-height:32px;border-radius:3px}
.or{font-size:11px;color:#7d8790}
.btn-social{height:32px;padding:0 14px;background:#3b5a9a;color:var(--white);font-size:12px;
  font-weight:600;line-height:32px;border-radius:3px;display:flex;align-items:center;gap:8px}
.btn-social i{width:14px;height:14px;background:var(--white);border-radius:2px;opacity:.85}

/* Footer */
.footer{position:absolute;left:0;top:1130px;width:867px;text-align:center;font-size:10px;color:#7d8790;line-height:17px}
</style>
</head>
<body>

<header class="hero">
  <div class="hero-photo" role="img" aria-label="Young man smiling while listening on headphones and holding a phone"></div>
  <div class="topbar">
    <div class="logo"><span class="logo-mark"></span>Dunmoral</div>
    <div class="login">Member Login</div>
  </div>
  <div class="hero-copy">
    <h1 class="headline">Unlimited Listening.</h1>
    <div class="subline">Wherever you are.</div>
    <div class="price">Only $9.99 per month</div>
    <div class="cta">Start Your Free Trial</div>
    <div class="cta-note">*Credit card not required</div>
  </div>
  <div class="dots"><span class="on"></span><span></span><span></span></div>
</header>

<h2 class="samples-title">A sample of what you can listen to on Dunmoral</h2>

<section class="grid">
  <div class="tile"><div class="tile-img" role="img" aria-label="Audiobook cover art" style="background:linear-gradient(135deg,#3a3a34,#a08a3a)"></div><div class="tile-label">Audio Books</div></div>
  <div class="tile"><div class="tile-img" role="img" aria-label="Comedian performing on stage" style="background:linear-gradient(135deg,#2a2230,#8a5a3a)"></div><div class="tile-label">Stand-Up Comedy</div></div>
  <div class="tile"><div class="tile-img" role="img" aria-label="French language course cover" style="background:linear-gradient(135deg,#1c5fa8,#6fb0e0)"></div><div class="tile-label">Language Learning</div></div>
  <div class="tile"><div class="tile-img" role="img" aria-label="Biography cover with portrait" style="background:linear-gradient(135deg,#dfe6ea,#b9a48e)"></div><div class="tile-label">Biographies &amp; Memoirs</div></div>
  <div class="tile"><div class="tile-img" role="img" aria-label="Relaxation meditation cover" style="background:linear-gradient(135deg,#5a3a8a,#b58ad0)"></div><div class="tile-label">Guided Meditations</div></div>
  <div class="tile"><div class="tile-img" role="img" aria-label="Business speaker at a lectern" style="background:linear-gradient(135deg,#10243e,#3d6a9a)"></div><div class="tile-label">Business Training</div></div>
  <div class="tile"><div class="tile-img" role="img" aria-label="Celebrity interview portrait" style="background:linear-gradient(135deg,#1a1a1a,#6a6a6a)"></div><div class="tile-label">Celebrity Interviews</div></div>
  <div class="tile"><div class="tile-img" role="img" aria-label="Elliptical workout coach cover" style="background:linear-gradient(135deg,#d02a6a,#3a8ad0)"></div><div class="tile-label">Fitness Programs</div></div>
</section>

<section class="points">
  <div class="point"><div class="point-art" role="img" aria-label="Illustration of mobile devices"></div><p>Listen on your Zarno, Kelvo Pad or Orbix device.<b>Learn More</b></p></div>
  <div class="point"><div class="point-art" role="img" aria-label="Illustration of a price tag"></div><p>All you can enjoy for one low monthly price.<b>Learn More</b></p></div>
  <div class="point"><div class="point-art" role="img" aria-label="Illustration of a calendar"></div><p>No obligation. Cancel any time.<b>Learn More</b></p></div>
</section>

<section class="optin">
  <h2>Start Your Free Trial</h2>
  <p class="optin-note">You will get instant &amp; unlimited access to all the material on Dunmoral for 14 days. There is no obligation &amp; you can cancel at any time.<br><a href="#">Credit card not required to try it free</a></p>
  <div class="form-row">
    <div class="email">Enter Email Address</div>
    <div class="btn-access">Get Instant Access</div>
    <span class="or">or</span>
    <div class="btn-social"><i></i>Sign Up Using Chatterly</div>
  </div>
</section>

<footer class="footer">
  About | Help | Contact Us | Member Login | Privacy Policy | Terms of Service<br>
  © 2014 Dunmoral Inc. All Rights Reserved
</footer>

</body>
</html>
```